Brindovalle Business cards

Dear team, I need to get the design file to suit it to our team. The focus of the business card is the Automotive Market and the design must be in black colour and the logo must be in glossy black. On the front of the card I need to get the following info:

- Name and Surname
- Title
- eMail
- Phone Number
- Skype account
- domain address

```html
<!DOCTYPE html>
<html lang="es">
<head>
<meta charset="utf-8">
<title>Brindovalle Business Cards</title>
<link href="https://fonts.googleapis.com/css2?family=Montserrat:wght@300;400;600;700&display=swap" rel="stylesheet">
<style>
  :root {
    --page-bg: #1c1c1c;
    --card-bg: #2b2b2b;
    --card-back-dark: #151515;
    --card-back-light: #4a4a4a;
    --brand-red: #e3262b;
    --text-white: #f4f4f4;
    --text-soft: #e2e2e2;
  }
  * { margin: 0; padding: 0; box-sizing: border-box; }
  html, body {
    width: 1200px;
    height: 1186px;
    overflow: hidden;
    background: var(--page-bg);
    font-family: "Montserrat", sans-serif;
  }
  .sheet {
    width: 1200px;
    height: 1186px;
    display: flex;
    flex-direction: column;
    align-items: center;
    justify-content: center;
    gap: 46px;
  }
  .card {
    position: relative;
    width: 860px;
    height: 510px;
    border-radius: 28px;
    overflow: hidden;
    box-shadow: 0 18px 40px rgba(0,0,0,0.55);
  }
  /* back side */
  .card-back { background: var(--card-back-dark); }
  .pattern-field {
    position: absolute;
    inset: 0;
    background: linear-gradient(120deg, var(--card-back-light) 0%, #2a2a2a 40%, var(--card-back-dark) 100%);
  }
  .brand-mark {
    display: flex;
    align-items: center;
    gap: 18px;
  }
  .brand-square {
    width: 56px;
    height: 56px;
    background: var(--brand-red);
  }
  .brand-name {
    font-weight: 700;
    font-size: 56px;
    letter-spacing: -0.5px;
    color: var(--text-white);
    line-height: 1;
  }
  .card-back .brand-mark {
    position: absolute;
    left: 50%;
    top: 50%;
    transform: translate(-50%, -50%);
  }
  /* front side */
  .card-front { background: var(--card-bg); }
  .card-front .brand-mark {
    position: absolute;
    left: 60px;
    top: 50%;
    transform: translateY(-50%);
  }
  .card-front .brand-square { width: 46px; height: 46px; }
  .card-front .brand-name { font-size: 46px; }
  .divider {
    position: absolute;
    left: 492px;
    top: 120px;
    width: 2px;
    height: 270px;
    background: var(--brand-red);
  }
  .contact {
    position: absolute;
    left: 522px;
    top: 120px;
    color: var(--text-soft);
  }
  .person-name {
    font-weight: 700;
    font-size: 27px;
    color: var(--brand-red);
    letter-spacing: 0.5px;
    text-transform: uppercase;
  }
  .person-title {
    font-weight: 400;
    font-size: 19px;
    color: var(--text-white);
    margin-top: 2px;
    margin-bottom: 18px;
  }
  .contact-list { list-style: none; }
  .contact-item {
    display: flex;
    align-items: center;
    gap: 12px;
    font-size: 17px;
    font-weight: 400;
    line-height: 29px;
  }
  .contact-icon { width: 16px; height: 16px; flex: none; }
  .address {
    margin-top: 16px;
    font-size: 17px;
    line-height: 23px;
    color: var(--text-soft);
  }
</style>
</head>
<body>
<main class="sheet">
  <section class="card card-back" aria-label="Reverso de la tarjeta">
    <div class="pattern-field" role="img" aria-label="Glossy black repeating pattern of brand symbols"></div>
    <div class="brand-mark">
      <span class="brand-square"></span>
      <span class="brand-name">Brindovalle</span>
    </div>
  </section>

  <section class="card card-front" aria-label="Anverso de la tarjeta">
    <div class="brand-mark">
      <span class="brand-square"></span>
      <span class="brand-name">Brindovalle</span>
    </div>
    <div class="divider"></div>
    <div class="contact">
      <p class="person-name">Marco Lentini</p>
      <p class="person-title">Comercial</p>
      <ul class="contact-list">
        <li class="contact-item">
          <svg class="contact-icon" viewBox="0 0 16 16" aria-hidden="true"><path fill="var(--brand-red)" d="M3 1h3l1.5 4-2 1.3a9 9 0 0 0 4.2 4.2L11 8.5l4 1.5v3a2 2 0 0 1-2 2A12 12 0 0 1 1 3a2 2 0 0 1 2-2z"/></svg>
          600 12 34 56
        </li>
        <li class="contact-item">
          <svg class="contact-icon" viewBox="0 0 16 16" aria-hidden="true"><rect x="1" y="3" width="14" height="10" rx="1" fill="var(--brand-red)"/><path d="M1.5 3.5 8 9l6.5-5.5" stroke="var(--card-bg)" stroke-width="1.4" fill="none"/></svg>
          redazione@brindovalle.com
        </li>
        <li class="contact-item">
          <svg class="contact-icon" viewBox="0 0 16 16" aria-hidden="true"><circle cx="8" cy="8" r="7" fill="var(--brand-red)"/></svg>
          @brindovalle
        </li>
        <li class="contact-item">
          <svg class="contact-icon" viewBox="0 0 16 16" aria-hidden="true"><circle cx="8" cy="8" r="6.5" fill="none" stroke="var(--brand-red)" stroke-width="1.6"/><ellipse cx="8" cy="8" rx="2.8" ry="6.5" fill="none" stroke="var(--brand-red)" stroke-width="1.3"/><path d="M1.5 8h13" stroke="var(--brand-red)" stroke-width="1.3"/></svg>
          www.brindovalle.com
        </li>
      </ul>
      <p class="address">Pol. Ind. Norvela, C/4 nº 12<br>28900 Vallerosa</p>
    </div>
  </section>
</main>
</body>
</html>
```